Tour operator needs simple coded WordPress site (updated extra payment for coding and guaranteed)

[update 9/7/2015]
If you design a new logo and it gets accepted, even if we use another template with your logo you will get $50
[update 8/7/2015]
Update on questions about dual-language
For dual languages we are happy to set up a second site with the same designs in a second language.
For the design aspect just allow the user to switch between languages with an icon.
For the coding, a replica of the site on a second server will do (to save messing around with multiple language plugins) - we will populate it with Chinese text
[original post]
Simple coded WordPress site for tours
You can choose to design only or design and code ($340 design, $150 bonus for coding)
Open design brief - use your creativity
Will be in 2 languages (English and Chinese) but design needs only to be in one language
Winning design will be chosen only from home page, but the winner must make a second standard template page when chosen at no extra cost.
Must be responsive design
We only need homepage and standard template page design and coding, we will populate the pages
You can use design ideas from our pamphlet if you like - attached
Only a sample logo and colors on website and pamphlet - feel free to change as the current ones seem restrictive
Current website framework only to give an idea of the number of pages and basic menu structure (no need to use existing navigation style or any style at all for that matter, open brief)
http://brightwattlejourneys.com.au/
Target Market(s)
Chinese parents of kids 10-14 (the kids will take the tour)
Industry/Entity Type
Tour
Number of Pages Required
2 page
Look and feel
Each slider illustrates characteristics of the customer's brand and the style your logo design should communicate.

```html
<!DOCTYPE html>
<html lang="en">
<head>
<meta charset="utf-8">
<title>Bright Wattle Journeys</title>
<link href="https://fonts.googleapis.com/css2?family=Raleway:wght@400;500;600&family=Open+Sans:wght@400;600&display=swap" rel="stylesheet">
<style>
:root{
  --navy:#2c3577;
  --cyan:#14b8dc;
  --cyan-dark:#0aa2c8;
  --orange:#ffa800;
  --orange-btn:#f2a115;
  --green:#6e9b55;
  --title-blue:#1f8fc8;
  --text:#555;
  --muted:#8a8a8a;
  --white:#fff;
}
*{margin:0;padding:0;box-sizing:border-box}
html,body{width:846px;height:1200px;overflow:hidden;background:var(--white)}
body{position:relative;font-family:'Open Sans',sans-serif;color:var(--text)}
.abs{position:absolute}

/* header */
.brand{left:122px;top:22px;display:flex;align-items:center;gap:8px}
.brand-dot{width:26px;height:26px;border-radius:50%;background:var(--orange)}
.brand-name{font-family:'Raleway',sans-serif;font-weight:600;font-size:17px;color:var(--navy)}
.lang{left:650px;top:36px;width:70px;height:20px;border:1px solid #ddd;border-radius:2px;display:flex;align-items:center;gap:5px;padding-left:7px;font-size:8.5px;color:#333}
.lang-flag{width:13px;height:8px;background:linear-gradient(#c8102e,#c8102e) center/100% 2px no-repeat,linear-gradient(#c8102e,#c8102e) center/2px 100% no-repeat,#1f3b8f}

/* navigation */
.nav{left:0;top:67px;width:846px;height:33px;background:linear-gradient(#2bc6e6,#0fa9d2)}
.nav a{position:absolute;top:0;height:33px;line-height:33px;transform:translateX(-50%);font-family:'Raleway',sans-serif;font-weight:500;font-size:10.5px;color:var(--white);text-decoration:none;letter-spacing:.2px}
.nav i{position:absolute;top:0;width:1px;height:33px;background:rgba(255,255,255,.3)}

/* hero */
.hero{left:0;top:100px;width:846px;height:323px;background:linear-gradient(180deg,#2a2f9a 0%,#3a3ca8 35%,#7a4f7a 62%,#c9703a 80%,#4a3040 100%)}
.hero-kicker{left:121px;top:188px;font-family:'Raleway',sans-serif;font-size:16.5px;color:var(--white)}
.hero-title{left:121px;top:212px;font-family:'Raleway',sans-serif;font-weight:500;font-size:28px;color:var(--white)}
.hero-text{left:121px;top:250px;width:300px;font-size:7.5px;line-height:13px;color:var(--white)}
.dots{left:122px;top:286px;display:flex;gap:3px}
.dots span{width:11px;height:11px;border-radius:50%;background:var(--white)}
.dots span:first-child{background:var(--orange)}

/* services */
.service{top:445px;width:200px;text-align:center;transform:translateX(-50%)}
.service svg{display:block;margin:0 auto}
.service h3{margin-top:8px;font-family:'Raleway',sans-serif;font-weight:400;font-size:14px;color:#333}
.service p{margin-top:6px;font-size:6.8px;line-height:13.3px;color:var(--muted)}
.btn{display:inline-block;width:70px;height:21px;line-height:21px;border-radius:2px;font-size:7.5px;color:var(--white);text-align:center;text-transform:uppercase;box-shadow:0 1px 2px rgba(0,0,0,.25)}
.service .btn{margin-top:12px}
.btn-orange{background:var(--orange-btn)}
.btn-cyan{background:var(--cyan-dark)}
.btn-green{background:var(--green)}

/* about band */
.about{left:0;top:626px;width:846px;height:264px;background:var(--orange)}
.about-photo{left:410px;top:626px;width:436px;height:264px;background:linear-gradient(90deg,var(--orange) 0%,#e39a2a 20%,#b9743f 45%,#6d4c52 70%,#3b3a55 100%)}
.about-title{left:124px;top:680px;font-family:'Raleway',sans-serif;font-weight:500;font-size:19px;color:var(--white)}
.about-lead{left:124px;top:708px;width:360px;font-size:9px;line-height:13.5px;color:var(--white)}
.about-text{left:124px;top:740px;width:360px;font-size:6.4px;line-height:13.4px;color:var(--white)}
.about-text p+p{margin-top:3px}
.about .btn,.about-btn{left:124px;top:806px;width:75px}

/* cards */
.card{top:925px;width:185px}
.card-img{width:185px;height:85px}
.card h3{margin-top:10px;font-family:'Raleway',sans-serif;font-weight:400;font-size:14px;color:var(--title-blue)}
.card p{margin-top:4px;font-size:6.8px;line-height:13.3px;color:var(--muted)}

/* footer */
.footer{left:0;top:1125px;width:846px;height:75px;background:linear-gradient(#fafafa,#ececec);border-top:1px solid #e2e2e2}
.footer-links{left:130px;top:1148px;font-family:'Raleway',sans-serif;font-weight:500;font-size:8.3px;color:#333;letter-spacing:.2px}
.footer-copy{left:130px;top:1166px;font-size:6.4px;color:#444}
.social{left:665px;top:1146px;display:flex;gap:6px}
.social span{width:11px;height:11px;border-radius:50%;background:var(--cyan-dark)}
</style>
</head>
<body>

<header>
  <div class="abs brand"><span class="brand-dot"></span><span class="brand-name">Bright Wattle Journeys</span></div>
  <div class="abs lang"><span class="lang-flag"></span>English
    <svg width="7" height="5" viewBox="0 0 7 5" style="margin-left:4px"><path d="M0 0h7L3.5 5z" fill="#555"/></svg>
  </div>
</header>

<nav class="abs nav">
  <a style="left:168px">HOME</a><i style="left:205px"></i>
  <a style="left:252px">ABOUT US</a><i style="left:297px"></i>
  <a style="left:339px">TOURS</a><i style="left:377px"></i>
  <a style="left:424px">SERVICES</a><i style="left:468px"></i>
  <a style="left:510px">TRAVEL</a><i style="left:549px"></i>
  <a style="left:606px">CONTACT US</a>
</nav>

<section>
  <div class="abs hero" role="img" aria-label="Night city skyline with lit towers and a bridge over the river"></div>
  <div class="abs hero-kicker">Donec dictum lectus non</div>
  <h1 class="abs hero-title">Australian Culture</h1>
  <p class="abs hero-text">Curabitur iaculis tempus eros Curabitur vel mi sit amet magna malesuada ultrices Ut nisi erat fermentum vel congue id euismod in elit</p>
  <div class="abs dots"><span></span><span></span><span></span><span></span></div>
</section>

<section>
  <div class="abs service" style="left:212px">
    <svg width="38" height="38" viewBox="0 0 38 38"><path d="M33 5c-2-2-5 0-7 2l-5 5-14-4-3 3 11 7-6 6-5-1-2 2 6 3 3 6 2-2-1-5 6-6 7 11 3-3-4-14 5-5c2-2 4-5 2-7z" fill="#f08a1a"/></svg>
    <h3>Educational Tours</h3>
    <p>Curabitur iaculis tempus eros Curabitur vel mi sit amet magna malesuada ultrices Ut nisi erat fermentum vel congue id euismod in elit</p>
    <span class="btn btn-orange">Read more</span>
  </div>
  <div class="abs service" style="left:428px">
    <svg width="38" height="38" viewBox="0 0 38 38"><path d="M19 4C10 4 3 10 2 18c2-2 5-2 7 0 2-2 5-2 7 0 2-2 4-2 6 0 2-2 5-2 7 0 2-2 5-2 7 0-1-8-8-14-17-14z" fill="#13a9d3"/><path d="M19 17v14a3 3 0 0 1-6 0" stroke="#13a9d3" stroke-width="2.4" fill="none" stroke-linecap="round"/></svg>
    <h3>Travel Insurance</h3>
    <p>Curabitur iaculis tempus eros Curabitur vel mi sit amet magna malesuada ultrices Ut nisi erat fermentum vel congue id euismod in elit</p>
    <span class="btn btn-cyan">Read more</span>
  </div>
  <div class="abs service" style="left:645px">
    <svg width="40" height="40" viewBox="0 0 40 40"><circle cx="20" cy="20" r="16" fill="none" stroke="#5f9a5a" stroke-width="6"/><circle cx="20" cy="20" r="16" fill="none" stroke="#fff" stroke-width="6.4" stroke-dasharray="5 20.1" stroke-dashoffset="-10"/><circle cx="20" cy="20" r="19.5" fill="none" stroke="#5f9a5a" stroke-width="1"/><circle cx="20" cy="20" r="12.5" fill="none" stroke="#5f9a5a" stroke-width="1"/></svg>
    <h3>Safety &amp; Security</h3>
    <p>Curabitur iaculis tempus eros Curabitur vel mi sit amet magna malesuada ultrices Ut nisi erat fermentum vel congue id euismod in elit</p>
    <span class="btn btn-green">Read more</span>
  </div>
</section>

<section>
  <div class="abs about"></div>
  <div class="abs about-photo" role="img" aria-label="Harbour at sunset with the opera house and the arch bridge reflected in the water"></div>
  <h2 class="abs about-title">About Bright Wattle Journeys</h2>
  <p class="abs about-lead">Curabitur iaculis tempus eros Curabitur vel mi sit amet magna malesuada ultrices Ut nisi erat fermentum vel congue id euismod in elit</p>
  <div class="abs about-text">
    <p>Morbi ornare gravida elit Integer congue augue et malesuada iaculis ipsum dui aliquet felis at cursus magna nisl nec elit Praesent elementum elit at tellus nec ultricies sit amet porttitor mattis enim in massa libero Interdum nec interdum vel blandit sed nulla In ullamcorper es</p>
    <p>Class aptent taciti sociosqu ad litora torquent per conubia nostra per inceptos hymenaeos</p>
  </div>
  <span class="abs btn btn-green about-btn">Read more</span>
</section>

<section>
  <article class="abs card" style="left:122px">
    <div class="card-img" role="img" aria-label="Kangaroos silhouetted against a golden sunset" style="background:linear-gradient(180deg,#6a5a3a,#e2a43a 60%,#3a2a14)"></div>
    <h3>Why Choose Us</h3>
    <p>Vivamus porttitor purus nisi eleifend libero a tempus libero lectus feugiat felis Morbi diam mauris viverra in gravida eu mattis in ante Morbi eget</p>
  </article>
  <article class="abs card" style="left:327px">
    <div class="card-img" role="img" aria-label="Young traveller with a backpack in front of a clock tower" style="background:linear-gradient(180deg,#3f86d8,#8fc0ec 60%,#6a8a4a)"></div>
    <h3>Featured Tour</h3>
    <p>Vivamus porttitor purus nisi eleifend libero a tempus libero lectus feugiat felis Morbi diam mauris viverra in gravida eu mattis in ante Morbi eget</p>
  </article>
  <article class="abs card" style="left:539px">
    <div class="card-img" role="img" aria-label="Group of students studying together outdoors" style="background:linear-gradient(180deg,#8fb8de,#6f8a6a 55%,#3c5a3a)"></div>
    <h3>Our Education &amp; Culture</h3>
    <p>Vivamus porttitor purus nisi eleifend libero a tempus libero lectus feugiat felis Morbi diam mauris viverra in gravida eu mattis in ante Morbi eget</p>
  </article>
</section>

<footer>
  <div class="abs footer"></div>
  <div class="abs footer-links">HOME &nbsp;|&nbsp; ABOUT US &nbsp;|&nbsp; SERVICES &nbsp;|&nbsp; TOUR &nbsp;|&nbsp; TRAVEL &nbsp;|&nbsp; CONTACT</div>
  <div class="abs footer-copy">© 2015 Company Name &nbsp;All right reserved &nbsp;Term of Use</div>
  <div class="abs social"><span></span><span></span><span></span><span></span></div>
</footer>

</body>
</html>
```